Meridian Tidewren Pale Ale Beer Label/Badge

We need a Beer Label designed for our first official beer to be launched under The meridian Brand!!
It will be a Pale Ale Called "Tidewren Pale Ale"!

The Meridian has the largest Craft Beer & Cider selection in the Geelong & Surf Coast region. With a funky location and a relaxed vibe, Meridian prides itself on serving delicious, unique seasonal food paired with Australia's best Craft Beer. The meridian is the perfect setting for a relaxed afternoon or evening with friends and can package an experience for larger groups or corporate bookings.

The Meridian Tavern brand has been growing for over a year and a half and the first label needs to integrate The meridian Logo but at the same time bring a fresh, new and eye catching feel to it along with embracing the "Odysseus" story in which we will be naming future beers.

The story of Tidewren is found via the following link
http://lorevault.example/wiki/Tidewren_(folklore)

We expect designers to research The meridian Tavern brand along with the all important Craft Beer Market and demographics. This will, potentially, be the start of many more labels to come for the winning designer!!

Requirements
Must have
• The original "O" needs to be integrated into the new logo and as much as the Greek mythology is being used it needs to be certain that this is an original Australian Craft Beer in the modern age!!
strong, modern & unique!!
Nice to have
• Logo could have a depiction of Tidewren
Should not have
• tackiness or cheap!!

```html
<!DOCTYPE html>
<html lang="en">
<head>
<meta charset="utf-8">
<title>Meridian Tidewren Pale Ale – Label</title>
<link rel="stylesheet" href="https://fonts.googleapis.com/css2?family=Jost:wght@400;500;700&family=Righteous&display=swap">
<style>
  :root {
    --page: #ffffff;
    --label-red: #8e2724;
    --label-charcoal: #353538;
    --title-ink: #2c2c30;
    --pale-cream: #e6dca4;
    --ale-red: #8e2724;
    --crest-blush: #ecdad8;
    --brand-grey: #8a939e;
    --brand-dot: #8e2724;
  }
  * { margin: 0; padding: 0; box-sizing: border-box; }
  html, body {
    width: 991px; height: 1200px; overflow: hidden;
    background: var(--page);
  }
  .canvas { position: relative; width: 991px; height: 1200px; }
  .label {
    position: absolute; left: 165px; top: 70px;
    width: 660px; height: 1060px;
    background: var(--label-charcoal);
    overflow: hidden;
  }
  .label__top {
    position: absolute; left: 0; top: 0;
    width: 660px; height: 579px;
    background: var(--label-red);
  }
  .label__title {
    position: absolute; left: 0; top: 0; width: 660px; height: 260px;
  }
  .label__title text {
    font-family: "Righteous", sans-serif;
    font-size: 68px; letter-spacing: 4px;
    fill: var(--title-ink);
  }
  .label__crest {
    position: absolute; left: 278px; top: 190px;
    width: 262px; height: 296px;
    background: var(--crest-blush);
    border-radius: 130px 130px 40px 60px;
  }
  .style-name {
    position: absolute; line-height: 1;
    font-family: "Jost", sans-serif;
    letter-spacing: -4px;
  }
  .style-name--pale {
    left: 26px; top: 436px;
    font-size: 166px; font-weight: 500;
    color: var(--pale-cream);
  }
  .style-name--ale {
    left: 118px; top: 560px;
    font-size: 172px; font-weight: 700;
    color: var(--ale-red);
  }
  .brand {
    position: absolute; left: 56px; top: 904px;
    display: flex; align-items: center; gap: 46px;
  }
  .brand__dot {
    width: 104px; height: 104px; border-radius: 50%;
    background: var(--brand-dot);
  }
  .brand__text {
    font-family: "Jost", sans-serif; font-weight: 500;
    color: var(--brand-grey); line-height: 1;
  }
  .brand__name { font-size: 70px; letter-spacing: 6px; }
  .brand__sub { margin-top: 12px; font-size: 23px; letter-spacing: 5.5px; padding-left: 6px; }
</style>
</head>
<body>
<main class="canvas">
  <section class="label" aria-label="Tidewren Pale Ale label">
    <div class="label__top"></div>
    <svg class="label__title" viewBox="0 0 660 260" aria-label="Tidewren">
      <defs>
        <path id="title-arc" d="M270 222 Q440 130 612 222"/>
      </defs>
      <text text-anchor="middle"><textPath href="#title-arc" startOffset="50%">TIDEWREN</textPath></text>
    </svg>
    <div class="label__crest" role="img" aria-label="Illustration of a Greek crested warrior helmet in profile"></div>
    <div class="style-name style-name--pale">PALE</div>
    <div class="style-name style-name--ale">ALE</div>
    <div class="brand">
      <div class="brand__dot"></div>
      <div class="brand__text">
        <div class="brand__name">MERIDIAN</div>
        <div class="brand__sub">TAVERN + BREWERY</div>
      </div>
    </div>
  </section>
</main>
</body>
</html>
```